Residential Remodeling Contractor needs updated business card

I need a new design for my business card.
Name of the company is Ridgefell Construction. I need a card that commands presence, strength, integrity. I have been in business for 28 years. I am a Residential Remodeling Contractor that covers all aspects of a residential remodel and build.

```html
<!DOCTYPE html>
<html lang="en">
<head>
<meta charset="utf-8">
<title>Ridgefell Construction – Business Card</title>
<link href="https://fonts.googleapis.com/css2?family=Montserrat:wght@400;600&display=swap" rel="stylesheet">
<style>
  :root{
    --brand-blue:#223f85;
    --brand-blue-soft:#5670b3;
    --paper:#ffffff;
    --ink:#1d1d1f;
    --backdrop:#dcdcdf;
  }
  *{box-sizing:border-box;margin:0;padding:0}
  html,body{width:1200px;height:786px;overflow:hidden}
  body{background:var(--backdrop);font-family:"Montserrat",sans-serif;position:relative}
  .card{position:absolute;top:245px;width:520px;height:297px;overflow:hidden;box-shadow:0 6px 18px rgba(0,0,0,.18)}
  .card--front{left:50px;background:var(--paper)}
  .card--back{left:630px;background:var(--brand-blue)}
  .front-panel{position:absolute;inset:0}
  .company-name{position:absolute;font-family:"Montserrat",sans-serif;font-weight:600;white-space:nowrap}
  .card--front .company-name{left:318px;top:118px;font-size:15px;color:var(--paper)}
  .card--back .company-name{right:44px;top:130px;font-size:28px;color:var(--brand-blue-soft)}
  .holder{position:absolute;left:34px;top:52px}
  .holder-name{color:var(--brand-blue);font-weight:600;font-size:19px}
  .holder-role{color:var(--ink);font-size:10px;margin-top:3px;margin-left:6px}
  .address{position:absolute;left:40px;top:160px;font-size:11px;color:var(--ink);line-height:1.3}
  .contacts{position:absolute;left:34px;top:222px;list-style:none;font-size:11px;color:var(--ink)}
  .contacts li{display:flex;align-items:center;gap:10px;height:20px}
  .contacts svg{width:12px;height:12px;fill:var(--brand-blue)}
</style>
</head>
<body>
  <section class="card card--front" aria-label="Business card front">
    <svg class="front-panel" viewBox="0 0 520 297" aria-hidden="true">
      <polygon points="205,0 520,0 520,297 355,297" fill="var(--brand-blue)"/>
    </svg>
    <p class="company-name">Ridgefell Construction</p>
    <div class="holder">
      <p class="holder-name">Daniel Hartwell</p>
      <p class="holder-role">Owner</p>
    </div>
    <p class="address">417 Quarry Stone Road<br>Clinton, MS 39056</p>
    <ul class="contacts">
      <li><svg viewBox="0 0 24 24"><path d="M6.6 10.8a15.1 15.1 0 0 0 6.6 6.6l2.2-2.2a1 1 0 0 1 1-.25 11.4 11.4 0 0 0 3.6.57 1 1 0 0 1 1 1V20a1 1 0 0 1-1 1A17 17 0 0 1 3 4a1 1 0 0 1 1-1h3.5a1 1 0 0 1 1 1c0 1.25.2 2.45.57 3.57a1 1 0 0 1-.25 1z"/></svg>555.214.7730</li>
      <li><svg viewBox="0 0 24 24"><path d="M2 5h20v14H2zm2 2v.5l8 5 8-5V7l-8 5z"/></svg>info@ridgefellconstruction.com</li>
      <li><svg viewBox="0 0 24 24"><path d="M12 2a10 10 0 1 0 0 20 10 10 0 0 0 0-20zm6.9 9h-3a15 15 0 0 0-1.3-5.6A8 8 0 0 1 18.9 11zM12 4c.9 1.2 1.8 3.6 1.9 7h-3.8c.1-3.4 1-5.8 1.9-7zM9.4 5.4A15 15 0 0 0 8.1 11h-3a8 8 0 0 1 4.3-5.6zM5.1 13h3a15 15 0 0 0 1.3 5.6A8 8 0 0 1 5.1 13zM12 20c-.9-1.2-1.8-3.6-1.9-7h3.8c-.1 3.4-1 5.8-1.9 7zm2.6-1.4a15 15 0 0 0 1.3-5.6h3a8 8 0 0 1-4.3 5.6z"/></svg>www.ridgefellconstruction.com</li>
    </ul>
  </section>

  <section class="card card--back" aria-label="Business card back">
    <p class="company-name">Ridgefell Construction</p>
  </section>
</body>
</html>
```